Inspiring Fundraising Foundation Website to Provide Academic Scholarships

Hello, we are launching a foundation to provide academic scholarships to high school students for college. We'd like this to be an informational website with contact information. There will be a total of approximately 5-7 pages in all.
The color scheme will be purple and white, with a girly feel. I 've attached the logo for reference!

Target Market(s)

high school students, college students

Industry/Entity Type

Education

Coding

Coded - Design and coding required

Number of Pages Required

5+ page

Font styles to use
Serif
Sans Serif
Script

Colors
6b449b
886aae
b7a5cd
e4daeb
ffffff
fdf9cf
fbf289

Requirements
Must have
• Purple, girly feel, to reflect the logo's style. Should be light-themed
Should not have
• No dark themes (aka heavy on black or dark colors)

```html
<!DOCTYPE html>
<html lang="en">
<head>
<meta charset="utf-8">
<title>Elena Varga Foundation</title>
<link rel="stylesheet" href="https://fonts.googleapis.com/css2?family=Raleway:wght@400;500;600;700&family=Open+Sans:ital,wght@0,400;0,600;1,400&display=swap">
<style>
:root{
  --purple:#6b449b;
  --purple-deep:#4a2670;
  --purple-mid:#886aae;
  --purple-soft:#b7a5cd;
  --purple-pale:#e4daeb;
  --white:#ffffff;
  --ink:#333333;
  --text:#666666;
  --muted:#999999;
  --line:#dddddd;
  --footer:#ececec;
  --footer-bar:#e2e2e2;
  --play:#e0474c;
}
*{box-sizing:border-box;margin:0;padding:0}
html,body{width:696px;height:1200px;overflow:hidden;background:var(--white)}
body{position:relative;font-family:"Open Sans",sans-serif;color:var(--text);font-size:7px}
.abs{position:absolute}
.heading{font-family:"Raleway",sans-serif;color:var(--ink);font-weight:600}
.photo{background:linear-gradient(135deg,#d9cfc3,#b9b0a6)}
.framed{border:1px solid var(--line);padding:3px;background:var(--white);box-shadow:0 1px 2px rgba(0,0,0,.06)}
.framed .photo{width:100%;height:100%}
.btn{background:var(--purple-mid);color:var(--white);font-family:"Raleway",sans-serif;font-weight:700;font-size:7px;text-transform:uppercase;display:flex;align-items:center;justify-content:center;border-radius:2px}

/* header */
.site-header{left:0;top:0;width:696px;height:67px;border-bottom:1px solid #e5e5e5;background:var(--white);box-shadow:0 1px 3px rgba(0,0,0,.05)}
.brand{left:52px;top:12px;width:60px;font-family:"Raleway",sans-serif;font-weight:700;color:var(--purple);font-size:11px;line-height:12px;text-align:center}
.brand-dot{width:11px;height:11px;border-radius:50%;background:var(--purple);margin:0 auto 3px}
.brand small{display:block;font-size:5px;letter-spacing:1.5px;font-weight:600;margin-top:2px}
.topbar{left:210px;top:15px;font-size:7px;color:var(--text);display:flex;gap:14px;align-items:center}
.topbar b{color:var(--purple);font-weight:400}
.topbar svg{width:7px;height:7px;margin-right:3px;vertical-align:-1px}
.search{left:470px;top:12px;width:116px;height:17px;border:1px solid var(--line);font-size:6px;color:var(--muted);padding:4px 6px}
.login{left:592px;top:12px;width:46px;height:17px;font-size:6px}
.nav{left:171px;top:48px;width:468px;display:flex;justify-content:space-between;font-family:"Raleway",sans-serif;font-weight:600;font-size:6.4px;color:#555;text-transform:uppercase}

/* hero */
.hero{left:0;top:67px;width:696px;height:337px;
  background:
    radial-gradient(ellipse 120px 150px at 610px 250px,#e0559a 0%,rgba(224,85,154,.85) 45%,rgba(224,85,154,0) 100%),
    radial-gradient(ellipse 70px 80px at 480px 90px,#6a4e3e 0%,rgba(106,78,62,.6) 50%,rgba(106,78,62,0) 100%),
    radial-gradient(ellipse 110px 70px at 380px 170px,#9aa0ad 0%,rgba(154,160,173,0) 100%),
    radial-gradient(ellipse 140px 60px at 520px 320px,#eeeef2 0%,rgba(238,238,242,0) 100%),
    linear-gradient(90deg,#f0f0f2 0%,#e2e3e7 45%,#d3d3d8 70%,#c7c2c6 100%)}
.hero-title{left:58px;top:154px;font-family:"Raleway",sans-serif;color:var(--purple-deep);font-weight:700;line-height:1}
.hero-title .l1{font-size:27px}
.hero-title .l2{font-size:21px;margin-top:4px}
.hero-sub{left:58px;top:216px;width:320px;font-family:"Raleway",sans-serif;font-size:13px;line-height:20px;color:#555;text-transform:uppercase}
.hero-btn{left:58px;top:264px;width:87px;height:25px;box-shadow:0 2px 3px rgba(0,0,0,.15)}

/* welcome */
.welcome-photo{left:58px;top:439px;width:166px;height:117px}
.welcome-photo .photo{background:
  radial-gradient(ellipse 30px 70px at 83px 75px,#2a2020 0%,rgba(42,32,32,.8) 50%,rgba(42,32,32,0) 100%),
  linear-gradient(180deg,#f3ebe7 0%,#eadfd9 70%,#c9443f 80%,#b83a36 100%)}
.welcome-title{left:250px;top:442px;font-size:13px;color:#333}
.welcome-text{left:250px;top:466px;width:372px;font-size:6.6px;line-height:14.4px}
.welcome-btn{left:251px;top:532px;width:64px;height:20px}

/* cards */
.card{top:591px;width:188px;height:115px;overflow:hidden}
.card .photo{position:absolute;inset:0}
.card-label{position:absolute;left:0;bottom:0;width:122px;height:36px;background:rgba(107,68,155,.88);color:var(--white);padding:7px 12px}
.card-label h3{font-family:"Raleway",sans-serif;font-weight:600;font-size:8px;text-transform:uppercase}
.card-label p{font-size:6px;margin-top:2px}

/* content columns */
.col-title{font-size:10px;text-transform:uppercase;color:#222}
.arrows{font-size:7px;color:var(--muted);letter-spacing:4px}
.news-item{left:58px;width:210px;height:52px}
.news-item .framed{position:absolute;left:0;top:0;width:73px;height:52px}
.news-body{position:absolute;left:84px;top:2px;width:126px}
.news-body h4{font-family:"Raleway",sans-serif;font-weight:700;font-size:6.2px;color:#222}
.news-body .date{color:var(--purple);font-size:5.8px;margin:4px 0 2px}
.news-body p{font-size:5.8px;line-height:12.5px}
.video{left:292px;top:761px;width:169px;height:105px;background:
  radial-gradient(ellipse 40px 55px at 85px 70px,#e98fc7 0%,rgba(233,143,199,.7) 50%,rgba(233,143,199,0) 100%),
  radial-gradient(ellipse 30px 60px at 150px 70px,#8a9aae 0%,rgba(138,154,174,0) 100%),
  radial-gradient(ellipse 30px 60px at 20px 70px,#7a8a7a 0%,rgba(122,138,122,0) 100%),
  linear-gradient(180deg,#a9c46a 0%,#7fa84d 60%,#6e9444 100%)}
.play{position:absolute;left:71px;top:39px;width:27px;height:27px;border-radius:50%;background:var(--play)}
.quote{left:495px;top:770px;width:128px;font-style:italic;font-size:6.2px;line-height:12.5px}
.quote-mark{font-family:Georgia,serif;font-size:16px;color:var(--muted)}
.author-photo{left:499px;top:832px;width:30px;height:30px;border-radius:50%;border:2px solid #eee;background:radial-gradient(circle at 50% 40%,#d8b8a0 0%,#8a7060 60%,#5a4a40 100%)}
.author{left:538px;top:836px;font-family:"Raleway",sans-serif}
.author b{color:var(--purple);font-size:7px;font-weight:600}
.author i{display:block;font-family:"Open Sans",sans-serif;font-size:6.5px;color:var(--muted);margin-top:4px}
.thumb{top:907px;width:83px;height:60px}

/* footer */
.site-footer{left:0;top:1003px;width:696px;height:169px;background:var(--footer)}
.fcol{top:1026px}
.fcol h5{font-family:"Raleway",sans-serif;font-size:7.2px;font-weight:600;color:var(--purple);text-transform:uppercase;width:97px;padding-bottom:5px;border-bottom:1px solid var(--purple-mid);margin-bottom:7px}
.fcol ul{list-style:none;font-size:6.2px;line-height:12.9px}
.fcol p{font-size:6.2px;line-height:12.9px}
.fcol .org{font-weight:600;color:#555;font-size:6.6px;margin-bottom:2px}
.fcol svg{width:6px;height:6px;margin-right:4px;vertical-align:-1px}
.social{display:flex;gap:5px;margin-top:9px}
.social span{width:17px;height:17px;border-radius:50%;background:var(--purple);box-shadow:inset 0 0 0 2px var(--purple-mid)}
.copyright{left:0;top:1172px;width:696px;height:28px;background:var(--footer-bar);text-align:center;font-size:6.4px;line-height:28px;color:#777}
</style>
</head>
<body>

<header class="abs site-header">
  <div class="abs brand"><div class="brand-dot"></div>Elena<br>Varga</div>
  <div class="abs topbar">
    <span><svg viewBox="0 0 10 10"><path d="M2 0l2 2-1 2q1 2 3 3l2-1 2 2-2 2Q0 9 0 2z" fill="#886aae"/></svg>CALL US : <b>( 555 ) 014 - 2290</b></span>
    <span><svg viewBox="0 0 10 10"><rect x="0" y="2" width="10" height="6" fill="#886aae"/><path d="M0 2l5 3.5L10 2" fill="none" stroke="#fff" stroke-width="1"/></svg>Email Us : <b>info@elenavarga.org</b></span>
  </div>
  <div class="abs search">Search...</div>
  <div class="abs btn login">Login&nbsp;&nbsp;⌄</div>
  <nav class="abs nav">
    <span>About us</span><span>Learning platforms ⌄</span><span>Academic support ⌄</span><span>Scholarships ⌄</span><span>News room</span><span>Careers</span>
  </nav>
</header>

<section class="abs hero" role="img" aria-label="Photo of a smiling student in a pink top working on a laptop in a classroom"></section>
<div class="abs hero-title"><div class="l1">ELENA VARGA</div><div class="l2">FOUNDATION</div></div>
<p class="abs hero-sub">We provide academic scholarships to high school students for college</p>
<div class="abs btn hero-btn">Contact here!</div>

<div class="abs framed welcome-photo"><div class="photo" role="img" aria-label="Portrait of the foundation's namesake seated on a red sofa"></div></div>
<h2 class="abs heading welcome-title">WELCOME TO ELENA VARGA FOUNDATION</h2>
<p class="abs welcome-text">Elena Varga was a significant contributor to the beginning of Harlow and Company Properties. As one of the company's first employees, her plan was to work as an Administrative Assistant while she finished her undergraduate degree in Business Administration at Lakeside University. With plans to graduate in December of 2016, she couldn't wait to begin her real estate career, since she had just...</p>
<div class="abs btn welcome-btn">Read more</div>

<div class="abs card" style="left:58px"><div class="photo" style="background:radial-gradient(ellipse 60px 50px at 60px 40px,#e8c8a8 0%,rgba(232,200,168,0) 100%),radial-gradient(ellipse 40px 40px at 170px 20px,#a8d088 0%,rgba(168,208,136,0) 100%),linear-gradient(180deg,#efe8e0 0%,#d9cfc3 60%,#f4f2ee 100%)" role="img" aria-label="Students writing at desks"></div><div class="card-label"><h3>Learning platforms</h3><p>Click here for view info »</p></div></div>
<div class="abs card" style="left:254px"><div class="photo" style="background:radial-gradient(ellipse 60px 50px at 70px 45px,#c8a088 0%,rgba(200,160,136,0) 100%),radial-gradient(ellipse 50px 40px at 160px 90px,#606870 0%,rgba(96,104,112,0) 100%),linear-gradient(180deg,#f0a0c0 0%,#e6b0c6 40%,#d8d0cc 100%)" role="img" aria-label="Teacher helping students at computers"></div><div class="card-label"><h3>Academic support</h3><p>Click here for view info »</p></div></div>
<div class="abs card" style="left:451px"><div class="photo" style="background:radial-gradient(ellipse 50px 40px at 60px 60px,#4a70b8 0%,rgba(74,112,184,0) 100%),radial-gradient(ellipse 40px 40px at 150px 40px,#a05060 0%,rgba(160,80,96,0) 100%),linear-gradient(180deg,#e0e0a0 0%,#e8d8b8 60%,#f0c8c0 100%)" role="img" aria-label="Teacher with children at a table"></div><div class="card-label"><h3>Scholarships</h3><p>Click here for view info »</p></div></div>

<h3 class="abs heading col-title" style="left:58px;top:737px">Latest news</h3>
<span class="abs arrows" style="left:247px;top:739px">‹›</span>
<article class="abs news-item" style="top:766px"><div class="framed"><div class="photo" style="background:radial-gradient(ellipse 20px 15px at 48px 18px,#3a6aa8 0%,rgba(58,106,168,0) 100%),linear-gradient(135deg,#e8d8c8,#c8b0a0)" role="img" aria-label="Students studying together"></div></div><div class="news-body"><h4>LOREM IPSUM IS SIMPLY DUMMY TEXT</h4><p class="date">Posted on 27 march 2016</p><p>Lorem Ipsum is simply dummy text of the printing and typesetting industry.</p></div></article>
<article class="abs news-item" style="top:837px"><div class="framed"><div class="photo" style="background:radial-gradient(ellipse 15px 20px at 35px 25px,#b03030 0%,rgba(176,48,48,0) 100%),linear-gradient(90deg,#e89040,#d8b060 50%,#e07030)" role="img" aria-label="Student reading in a library"></div></div><div class="news-body"><h4>LOREM IPSUM IS SIMPLY DUMMY TEXT</h4><p class="date">Posted on 27 march 2016</p><p>Lorem Ipsum is simply dummy text of the printing and typesetting industry.</p></div></article>
<article class="abs news-item" style="top:907px"><div class="framed"><div class="photo" style="background:radial-gradient(ellipse 15px 12px at 45px 28px,#3a6ac8 0%,rgba(58,106,200,0) 100%),linear-gradient(135deg,#e8ecc8,#c8d0b0)" role="img" aria-label="Children in a classroom"></div></div><div class="news-body"><h4>LOREM IPSUM IS SIMPLY DUMMY TEXT</h4><p class="date">Posted on 27 march 2016</p><p>Lorem Ipsum is simply dummy text of the printing and typesetting industry.</p></div></article>

<h3 class="abs heading col-title" style="left:291px;top:737px">Our video</h3>
<div class="abs video" role="img" aria-label="Video still of students standing outdoors"><span class="play"><svg viewBox="0 0 27 27" width="27" height="27"><path d="M11 8l9 5.5-9 5.5z" fill="#fff"/></svg></span></div>

<h3 class="abs heading col-title" style="left:291px;top:884px">Photo gallery <span style="font-family:'Open Sans',sans-serif;font-weight:400;font-size:7px;color:#666;text-transform:none">&nbsp;Lorem Ipsum is simply dummy text of the printing</span></h3>
<span class="abs arrows" style="left:626px;top:886px">‹›</span>
<div class="abs framed thumb" style="left:292px"><div class="photo" style="background:radial-gradient(ellipse 20px 12px at 40px 35px,#d04040 0%,rgba(208,64,64,0) 100%),linear-gradient(135deg,#c87060,#e8d8c8)" role="img" aria-label="Gallery photo of a classroom"></div></div>
<div class="abs framed thumb" style="left:379px"><div class="photo" style="background:radial-gradient(ellipse 18px 25px at 38px 35px,#505860 0%,rgba(80,88,96,0) 100%),linear-gradient(135deg,#a8a098,#e0d8d0)" role="img" aria-label="Gallery photo of students"></div></div>
<div class="abs framed thumb" style="left:467px"><div class="photo" style="background:radial-gradient(ellipse 20px 18px at 40px 30px,#706058 0%,rgba(112,96,88,0) 100%),linear-gradient(135deg,#d8c8c0,#f0e8e0)" role="img" aria-label="Gallery photo of a lecture"></div></div>
<div class="abs framed thumb" style="left:555px"><div class="photo" style="background:radial-gradient(ellipse 18px 20px at 30px 35px,#4aa8e0 0%,rgba(74,168,224,0) 100%),linear-gradient(135deg,#d8e8a0,#e8c8b0)" role="img" aria-label="Gallery photo of children learning"></div></div>

<h3 class="abs heading col-title" style="left:481px;top:737px">Testimonials</h3>
<span class="abs arrows" style="left:626px;top:739px">‹›</span>
<span class="abs quote-mark" style="left:482px;top:763px">“</span>
<p class="abs quote">Lorem Ipsum is simply dummy text of the printing and typesetting industry. Lorem Ipsum has been the industry's standard dummy text ever since the 1500</p>
<span class="abs quote-mark" style="left:627px;top:807px">”</span>
<div class="abs author-photo" role="img" aria-label="Student portrait"></div>
<div class="abs author"><b>OWEN CASTELL</b><i>Student</i></div>

<footer class="abs site-footer"></footer>
<div class="abs fcol" style="left:58px"><h5>Welcome</h5><ul><li>Home</li><li>About us</li><li>Learning Platforms</li><li>Academic support</li><li>Scholarships</li><li>News Room</li><li>Careers</li></ul></div>
<div class="abs fcol" style="left:207px"><h5>Information</h5><ul><li>Terms &amp; Conditions</li><li>Privacy Policy</li><li>Disclaimer</li><li>Contact us</li><li>Sitemap</li></ul></div>
<div class="abs fcol" style="left:356px"><h5>Contact info</h5>
  <p class="org">Elena Varga Foundation</p>
  <p>1800 Linden Park Ave St.320<br>Fairview, Texas</p>
  <p style="margin-top:3px"><svg viewBox="0 0 10 10"><path d="M2 0l2 2-1 2q1 2 3 3l2-1 2 2-2 2Q0 9 0 2z" fill="#6b449b"/></svg>( 555 ) 014 - 2290</p>
  <p><svg viewBox="0 0 10 10"><rect x="2.5" y="0.5" width="5" height="2.5" fill="none" stroke="#6b449b"/><rect x="0" y="3" width="10" height="4" fill="#6b449b"/><rect x="2.5" y="6" width="5" height="3.5" fill="#fff" stroke="#6b449b"/></svg>( 555 ) 014 - 2290</p>
  <p><svg viewBox="0 0 10 10"><rect x="0" y="2" width="10" height="6" fill="#6b449b"/><path d="M0 2l5 3.5L10 2" fill="none" stroke="#fff" stroke-width="1"/></svg>info@elenavarga.org</p>
</div>
<div class="abs fcol" style="left:501px"><h5>Privacy policy</h5>
  <p style="width:138px">We are excited to announce the Elena Varga Foundation in honor of a fabulous angel. We hope to impact the lives of individuals in the same way her dynamic...</p>
  <div class="social" aria-label="Social network links"><span></span><span></span><span></span><span></span><span></span></div>
</div>
<div class="abs copyright">Copyright © 2017. Elena Varga Foundation. All rights reserved.</div>

</body>
</html>
```